LinkedIn Banner Design for B2B Consulting Firm

Take the already developed logo (attached) and incorporate it into a creative banner design for placement on LinkedIn (the social media platform targeting business users). The banner will be used on the firm's company profile page on LinkedIn (not yet created).

```html
<!DOCTYPE html>
<html lang="en">
<head>
<meta charset="utf-8">
<title>Fractional Marketing Services – Company Banner</title>
<link rel="stylesheet" href="https://fonts.googleapis.com/css2?family=Montserrat:wght@500;800&display=swap">
<style>
  :root {
    --canvas-bg: #d8d9db;
    --banner-deep: #1d4336;
    --banner-mid: #285442;
    --banner-light: #36604a;
    --text-light: #ffffff;
  }
  html, body {
    margin: 0;
    padding: 0;
    width: 1200px;
    height: 929px;
    overflow: hidden;
    background: var(--canvas-bg);
  }
  .canvas {
    position: relative;
    width: 1200px;
    height: 929px;
  }
  .banner {
    position: absolute;
    left: 20px;
    top: 321px;
    width: 1160px;
    height: 287px;
    border-radius: 12px;
    overflow: hidden;
  }
  .banner-backdrop {
    position: absolute;
    inset: 0;
    background:
      radial-gradient(ellipse at 72% 30%, rgba(70,120,90,0.35), transparent 55%),
      radial-gradient(ellipse at 15% 80%, rgba(20,55,42,0.6), transparent 60%),
      linear-gradient(120deg, var(--banner-deep) 0%, var(--banner-mid) 55%, var(--banner-light) 100%);
  }
  .banner-copy {
    position: absolute;
    inset: 0;
    text-align: center;
    color: var(--text-light);
    font-family: "Montserrat", sans-serif;
  }
  .banner-title {
    margin: 0;
    position: absolute;
    left: 0;
    right: 0;
    top: 80px;
    font-weight: 800;
    font-size: 44px;
    letter-spacing: 0.5px;
    line-height: 1;
  }
  .banner-subtitle {
    position: absolute;
    left: 0;
    right: 0;
    font-weight: 500;
    font-size: 27px;
    line-height: 1;
    margin: 0;
  }
  .banner-subtitle.line-one { top: 145px; }
  .banner-subtitle.line-two {
    top: 178px;
    display: flex;
    justify-content: center;
    align-items: center;
    gap: 10px;
  }
  .rule {
    display: inline-block;
    width: 76px;
    height: 2px;
    background: var(--text-light);
  }
</style>
</head>
<body>
  <div class="canvas">
    <section class="banner">
      <div class="banner-backdrop" role="img" aria-label="Dark green background with a faint blurred photo of financial charts"></div>
      <div class="banner-copy">
        <h1 class="banner-title">FRACTIONAL MARKETING SERVICES</h1>
        <p class="banner-subtitle line-one">Private Equity Firm, Family Offices &amp;</p>
        <p class="banner-subtitle line-two"><span class="rule"></span>Investment Banks<span class="rule"></span></p>
      </div>
    </section>
  </div>
</body>
</html>
```